New Property development signage

large poster for a new development.
3 metres x 2 metres. To include the following.

Tresswick Gardens
TO LET
LUXURY FULLY FURNISHED LARGE
2 AND 3 BED APARTMENTS
Garrold Estates
362 4150
www.garroldestates-example.com

Need this to be large simple writing with Garrold estates logo on the bottom

Target Market(s)

High end rental property market

Industry/Entity Type

Real Estate Development

Colors
000000
cbcbcb
0555a3

Requirements
Must have
• Name of the development must be in a different font, classic style
Nice to have
• Light Grey background, blues for colours
Should not have
• anymore than 3 /4 colours

```html
<!DOCTYPE html>
<html lang="en">
<head>
<meta charset="utf-8">
<title>Tresswick Gardens – To Let</title>
<link rel="stylesheet" href="https://fonts.googleapis.com/css2?family=Libre+Baskerville:wght@700&family=Pinyon+Script&display=swap">
<style>
  :root {
    --bg: #cbcbcb;
    --brand-blue: #0555a3;
    --navy: #2b3990;
    --photo-warm: #d9c4a8;
    --photo-cool: #c9cfd6;
    --photo-wood: #c79a6a;
  }
  * { margin: 0; padding: 0; box-sizing: border-box; }
  html, body { width: 800px; height: 1200px; overflow: hidden; }
  body { background: var(--bg); font-family: "Libre Baskerville", Georgia, serif; }
  .poster { position: relative; width: 800px; height: 1200px; background: var(--bg); }
  .centered { position: absolute; left: 0; width: 800px; text-align: center; white-space: nowrap; }

  .development-name {
    top: 108px;
    font-family: "Pinyon Script", cursive;
    font-weight: 400;
    font-size: 84px;
    line-height: 1;
    color: var(--brand-blue);
  }
  .status {
    top: 246px;
    font-size: 34px;
    font-weight: 700;
    color: var(--brand-blue);
    letter-spacing: 0.5px;
  }
  .photo-grid {
    position: absolute;
    top: 318px; left: 135px;
    width: 537px; height: 240px;
    display: grid;
    grid-template-columns: repeat(3, 1fr);
    grid-template-rows: repeat(2, 1fr);
    gap: 2px;
    background: #ffffff;
  }
  .photo { width: 100%; height: 100%; }
  .photo--kitchen { background: linear-gradient(160deg, #e9ddc8 0%, var(--photo-warm) 55%, #8a6a4a 100%); }
  .photo--lounge { background: linear-gradient(180deg, #a9d6cf 0%, var(--photo-cool) 50%, var(--photo-wood) 100%); }
  .photo--living { background: linear-gradient(180deg, #f2ece0 0%, #e4d6c1 55%, var(--photo-wood) 100%); }
  .photo--bedroom { background: linear-gradient(180deg, #f1eee8 0%, #d9ccb4 55%, #5f79a8 100%); }
  .photo--sitting { background: linear-gradient(180deg, #efe9df 0%, #d8c4a6 55%, #9b6f55 100%); }
  .photo--guest { background: linear-gradient(180deg, #f3f0ea 0%, #ddd1bd 55%, #4d6fa6 100%); }

  .headline {
    font-size: 38px;
    font-weight: 700;
    color: var(--brand-blue);
    letter-spacing: -1px;
  }
  .headline--first { top: 615px; }
  .headline--second { top: 705px; }

  .phone {
    top: 798px;
    font-size: 54px;
    font-weight: 700;
    color: var(--navy);
    letter-spacing: 1px;
  }
  .agent-name {
    top: 912px;
    font-size: 42px;
    font-weight: 700;
    color: var(--navy);
  }
  .website {
    top: 1034px;
    font-size: 27px;
    font-weight: 700;
    color: var(--navy);
  }
</style>
</head>
<body>
  <main class="poster">
    <h1 class="centered development-name">Tresswick Gardens</h1>
    <p class="centered status">TO LET</p>

    <section class="photo-grid" aria-label="Apartment interiors">
      <div class="photo photo--kitchen" role="img" aria-label="Photo of a fitted kitchen with wooden cabinets and appliances"></div>
      <div class="photo photo--lounge" role="img" aria-label="Photo of a lounge with fireplace and bay window"></div>
      <div class="photo photo--living" role="img" aria-label="Photo of a living room with sofas and television"></div>
      <div class="photo photo--bedroom" role="img" aria-label="Photo of a bedroom with double bed and wardrobes"></div>
      <div class="photo photo--sitting" role="img" aria-label="Photo of a sitting room with fireplace and sofas"></div>
      <div class="photo photo--guest" role="img" aria-label="Photo of a second bedroom with double bed"></div>
    </section>

    <p class="centered headline headline--first">LUXURY FULLY FURNISED LARGE</p>
    <p class="centered headline headline--second">2 AND 3 BED APARTMENTS</p>

    <p class="centered phone">362 4150</p>
    <p class="centered agent-name">Garrold Estates</p>
    <p class="centered website">www.garroldestates-example.com</p>
  </main>
</body>
</html>
```